4th Generation Family Business Needs a New Card Design!

We are a family owned 4th Generation company. We are based in the Sydney, Australia area and we are desperately in need of a more modern and classy card. We are monumental masons who design, supply & erect lasting memorials throughout cemeteries in Sydney. Our customers are normally in a period of grieving. I have attached logo files that will need to be implemented on the card. Company was established 1935. Australian Owned and Operated. Card needs to be designed to PIXO.com specification.

Target Market(s)

Our target market is based upon people that a grieving for family members that have passed away. We also deal with alot of companies that own and operate cemeteries.

Industry/Entity Type

Business

Contact Information for Business Card

Simon Harcourt, Operations Manager, 0417293086, simon@harcourtmemorials.com.au
Lewis Harcourt, Director, 0491630572, lewis@harcourtmemorials.com.au
Phone # 02 9561 3048
Website: www.harcourtmemorials.com.au
Address: Suite 17, 8 Palfrey Lane, West Carlow, Sydney NSW 2156

Font styles to use
Serif
Decorative
Script

Requirements
Must have
• Would like to see the logo nicely implemented with a modern design. Embossed lettering would be a nice additive.

```html
<!DOCTYPE html>
<html lang="en">
<head>
<meta charset="utf-8">
<title>Harcourt Memorials – Business Card</title>
<link rel="stylesheet" href="https://fonts.googleapis.com/css2?family=Cinzel:wght@400;700&family=Open+Sans:wght@400&display=swap">
<style>
  :root {
    --backdrop: #d9dadc;
    --card-dark: #4a4a4a;
    --card-light: #f1f1ef;
    --silver: #e4e4e4;
    --ink: #1f1f1f;
    --gold: #e8b923;
    --white: #ffffff;
  }
  * { margin: 0; padding: 0; box-sizing: border-box; }
  html, body {
    width: 980px; height: 1200px; overflow: hidden;
    background: var(--backdrop);
  }
  .canvas { position: relative; width: 980px; height: 1200px; }
  .card {
    position: absolute;
    display: flex; flex-direction: column; align-items: center;
    text-align: center;
  }
  .card--front {
    left: 137px; top: 106px; width: 706px; height: 476px;
    background: var(--card-dark);
    padding-top: 116px;
  }
  .card--back {
    left: 127px; top: 627px; width: 714px; height: 476px;
    background: var(--card-light);
    padding-top: 58px;
  }
  .brand {
    display: flex; flex-direction: column; align-items: center;
    font-family: "Cinzel", serif;
    font-weight: 400;
    line-height: 1.05;
  }
  .brand__mark {
    width: 124px; height: 124px;
    margin-bottom: 18px;
  }
  .card--front .brand__mark { background: var(--silver); }
  .card--back .brand__mark { background: var(--ink); }
  .brand__name { font-size: 54px; letter-spacing: 1px; display: block; }
  .brand__sub { font-size: 24px; letter-spacing: 2px; display: block; }
  .card--front .brand { color: var(--silver); }
  .card--back .brand { color: var(--ink); }
  .address {
    margin-top: 34px;
    font-family: "Open Sans", sans-serif;
    font-size: 17px; line-height: 27px;
    color: var(--white);
  }
  .person__name {
    margin-top: 40px;
    font-family: "Cinzel", serif; font-weight: 700;
    font-size: 31px; letter-spacing: 1px;
    color: var(--ink);
  }
  .person__title {
    font-family: "Cinzel", serif; font-weight: 400;
    font-size: 19px; letter-spacing: 1px;
    color: var(--gold);
    margin-top: -2px;
  }
  .contact {
    margin-top: 16px;
    font-family: "Open Sans", sans-serif;
    font-size: 17px; line-height: 26px;
    color: var(--ink);
  }
</style>
</head>
<body>
<main class="canvas">
  <section class="card card--front">
    <div class="brand">
      <span class="brand__mark" aria-hidden="true"></span>
      <span class="brand__name">Harcourt</span>
      <span class="brand__sub">Memorials</span>
    </div>
    <p class="address">Suite 17, 8 Palfrey Lane<br>West Carlow, Sydney NSW 2156</p>
  </section>

  <section class="card card--back">
    <div class="brand">
      <span class="brand__mark" aria-hidden="true"></span>
      <span class="brand__name">Harcourt</span>
      <span class="brand__sub">Memorials</span>
    </div>
    <h1 class="person__name">Simon Harcourt</h1>
    <p class="person__title">Operations Manager</p>
    <p class="contact">02 9561 3048 &nbsp;| 0417293086 | simon@harcourtmemorials.com.au<br>www.harcourtmemorials.com.au</p>
  </section>
</main>
</body>
</html>
```